Business card design for a dynamic IT consulting company

We need a business card design for a young firm, specialized in the Telecommunications/Consulting industry. The name of the company is Quindor and Partners Business Consulting Ltd. (Short name: Quindor and Partnes)
Quindor = solve read reverse, so we aim to be uncomplicated and solution-oriented. The small pipe in our logo is also related to the word solve. So we need a new business card design, which is simple, eye catching and something non traditional (I would probably prefer a square shaped design rather than a rectangle, but open for suggestions). Attached our logo.

Target Market(s)

Usually our customers are Tier1 Telecoms providers (Q-Netra, Palorix, etc) and their executives.

Industry/Entity Type

Business

Contact Information for Business Card

Name: Bence Tolnavari
Email: b.tolnavari@quindor.hu
Web: www.quindor.hu
Mobile: +36 30 518 2769
Title: Managing Director

Optional:
Company name: Quindor and Partners Ltd.
Address: 1087 Budapest, Tolvenka str. 28/C, Hungary

Font styles to use
Other font styles liked:
• helveticaneue_medium, Prime Regular are used now.

Colors

Designer to choose colors to be used in the design.

Requirements
Must have
• I would like to have a 2 sided design.
Nice to have
• I thought if we make the logo a bit bigger (without the company name), that could go to the back with the company name below. I though, if the pipe in the logo is somehow touchable on the business card, would be nice and unique.

```html
<!DOCTYPE html>
<html lang="en">
<head>
<meta charset="utf-8">
<title>Quindor &amp; Partners – Business Card</title>
<link rel="stylesheet" href="https://fonts.googleapis.com/css2?family=Exo+2:wght@400;500&family=Open+Sans:wght@400;600&display=swap">
<style>
  :root {
    --backdrop: #3b3430;
    --card: #1b1c1e;
    --card-edge: #2aa3dc;
    --ink-white: #f2f2f2;
    --ink-soft: #d8d8d8;
    --ink-silver: #7d7f82;
    --accent-blue: #2ea4e0;
    --accent-magenta: #b0308f;
  }
  * { margin: 0; padding: 0; box-sizing: border-box; }
  html, body {
    width: 1200px; height: 715px; overflow: hidden;
    background: var(--backdrop);
  }
  .sheet {
    width: 1200px; height: 715px;
    display: flex; align-items: center; justify-content: center; gap: 40px;
  }
  .card {
    width: 540px; height: 340px;
    background: var(--card);
    border-radius: 6px;
    position: relative;
    box-shadow: 0 10px 30px rgba(0,0,0,.45);
  }
  .card--front {
    border-bottom: 6px solid var(--card-edge);
    border-right: 6px solid var(--card-edge);
    display: flex; align-items: center; justify-content: center;
  }
  .wordmark {
    font-family: "Exo 2", sans-serif;
    font-weight: 400;
    white-space: nowrap;
  }
  .card--front .wordmark {
    font-size: 46px;
    color: var(--ink-silver);
    letter-spacing: 0.5px;
  }
  .card--back {
    display: flex; align-items: center;
    padding: 0 34px 0 36px;
  }
  .card--back .wordmark {
    font-size: 27px;
    color: var(--ink-white);
    width: 240px;
  }
  .divider {
    width: 2px; height: 170px;
    background: var(--accent-magenta);
    margin: 0 22px 0 6px;
  }
  .contact {
    font-family: "Open Sans", sans-serif;
    color: var(--ink-soft);
    font-size: 12.5px;
    line-height: 1.45;
  }
  .contact__name {
    font-family: "Exo 2", sans-serif;
    font-weight: 500;
    font-size: 19px;
    letter-spacing: 1px;
    color: var(--accent-blue);
    text-transform: uppercase;
  }
  .contact__title { margin-bottom: 8px; }
  .contact__company {
    font-family: "Exo 2", sans-serif;
    font-weight: 500;
    font-size: 13px;
    color: var(--accent-blue);
    text-transform: uppercase;
    letter-spacing: .5px;
  }
  .contact__address { margin-bottom: 8px; }
  .contact__line { display: flex; align-items: center; gap: 8px; }
  .contact__line svg { width: 11px; height: 11px; flex: none; }
</style>
</head>
<body>
<main class="sheet">
  <section class="card card--front" aria-label="Card front">
    <span class="wordmark">Quindor &amp; Partners</span>
  </section>

  <section class="card card--back" aria-label="Card back">
    <span class="wordmark">Quindor &amp; Partners</span>
    <div class="divider"></div>
    <div class="contact">
      <div class="contact__name">Bence Tolnavari</div>
      <div class="contact__title">Managing Director</div>
      <div class="contact__company">Quindor and Partners Ltd.</div>
      <div class="contact__address">1087 Budapest, Tolvenka<br>str. 28/C, Hungary</div>
      <div class="contact__line">
        <svg viewBox="0 0 12 12" aria-hidden="true"><path d="M2.5 1 L4.5 1 L5.3 3.4 L4 4.4 Q5 6.8 7.6 8 L8.6 6.7 L11 7.5 L11 9.5 Q11 11 9.5 11 Q1 10.5 1 2.5 Q1 1 2.5 1Z" fill="var(--accent-blue)"/></svg>
        <span>+36 30 518 2769</span>
      </div>
      <div class="contact__line">
        <svg viewBox="0 0 12 12" aria-hidden="true"><rect x="1" y="2.5" width="10" height="7" rx="1" fill="var(--accent-blue)"/><path d="M1.5 3 L6 6.6 L10.5 3" stroke="var(--card)" stroke-width="1" fill="none"/></svg>
        <span>b.tolnavari@quindor.hu</span>
      </div>
      <div class="contact__line">
        <svg viewBox="0 0 12 12" aria-hidden="true"><g fill="none" stroke="var(--accent-blue)" stroke-width="1.1"><circle cx="6" cy="6" r="4.8"/><ellipse cx="6" cy="6" rx="2" ry="4.8"/><path d="M1.2 6 H10.8"/></g></svg>
        <span>www.quindor.hu</span>
      </div>
    </div>
  </section>
</main>
</body>
</html>
```